Podiatry clinic requires a modern revamp and editing of existing website.

I would like a fresh new look and updated information for my current business website. An easy to navigate site with prominent address and phone number for call to action. We are a podiatry clinic that focuses on general and sports podiatry.
I would like 4 pages; including Home page, About Us, Services & Contact.
www.brambleridgepodiatry.net

Target Market(s)

Active working professionals.

Industry/Entity Type

Medical

Coding

Coded - Design and coding required

Number of Pages Required

4 page

Font styles to use
Sans Serif

Colors
6b449b

Requirements
Must have
• A modern look with logo and active images; clean and uncluttered. Visible phone number and address for call to action.
• 4 pages - Home, About Us, Services, Contact.
• Home page - update address & service logos.
• About Us - update of personal information.
• Services - Revamp of existing page.
• Contact page to include Google map, email & phone number.
Nice to have
• Ability to add content easily; eg. a blog or adding video onto Home page.
• Link to Follow us page.

```html
<!DOCTYPE html>
<html lang="en">
<head>
<meta charset="utf-8">
<title>Bramble Ridge Podiatry</title>
<link href="https://fonts.googleapis.com/css2?family=Raleway:wght@300;400;500;700;800&family=Open+Sans:wght@400;600;700&display=swap" rel="stylesheet">
<style>
:root{
  --purple:#4c3494;
  --purple-soft:#6b449b;
  --green:#7cc225;
  --text:#555;
  --grey-bg:#f0f0f0;
  --white:#fff;
  --sky-top:#cfe6f7;
  --sea:#3aa6c9;
  --sand:#eadfce;
}
*{margin:0;padding:0;box-sizing:border-box}
html,body{width:1200px;height:2782px;overflow:hidden}
body{position:relative;font-family:"Open Sans",sans-serif;color:var(--text);background:var(--white)}
.abs{position:absolute}
a{text-decoration:none}

/* top bar */
.topbar{left:0;top:0;width:1200px;height:52px;background:var(--purple);color:var(--white);font-size:21px}
.topbar .addr{left:98px;top:11px;display:flex;align-items:center;gap:10px}
.topbar .social{right:80px;top:12px;font-size:20px}

/* header */
.header{left:0;top:52px;width:1200px;height:134px;background:var(--white)}
.logo-disc{left:72px;top:40px;width:210px;height:214px;border-radius:50%;background:var(--white);z-index:3}
.logo-name{left:100px;top:96px;z-index:4;font-family:"Raleway",sans-serif;font-weight:800;font-size:30px;line-height:36px;color:var(--purple);width:180px}
.nav a{position:absolute;top:54px;font-family:"Raleway",sans-serif;font-size:18px;letter-spacing:.5px;color:#555;white-space:nowrap}
.nav a.active{color:var(--purple)}
.head-phone{left:892px;top:44px;display:flex;align-items:center;gap:14px;font-weight:700;font-size:27px;color:var(--green)}
.icon-circle{width:52px;height:52px;border-radius:50%;background:var(--purple);display:flex;align-items:center;justify-content:center}

/* hero */
.hero{left:0;top:186px;width:1200px;height:574px;overflow:hidden;background:linear-gradient(180deg,var(--sky-top) 0%,#b6dcf3 38%,var(--sea) 55%,#8ccbe0 68%,var(--sand) 100%)}
.hero-feet{left:720px;top:60px;width:420px;height:560px;border-radius:210px 210px 0 0;background:linear-gradient(180deg,#c49474 0%,#b37a58 100%);opacity:.75;filter:blur(2px)}
.hero-title{left:78px;top:132px;width:600px;font-family:"Raleway",sans-serif;font-weight:800;font-size:47px;line-height:78px;color:var(--purple);text-transform:uppercase}
.hero-sub{left:80px;top:278px;width:360px;font-family:"Raleway",sans-serif;font-size:21px;line-height:31px;color:var(--purple-soft)}
.btn{display:inline-flex;align-items:center;justify-content:center;border-radius:30px;font-family:"Raleway",sans-serif;text-transform:uppercase}
.hero .btn{position:absolute;left:78px;top:400px;width:228px;height:59px;background:var(--purple);color:var(--white);font-size:25px}

/* treatments */
.treat{top:760px;height:260px;width:600px}
.treat.general{left:0;background:var(--purple)}
.treat.special{left:600px;background:var(--green)}
.treat .photo{left:76px;top:32px;width:186px;height:186px;border-radius:50%;border:5px solid var(--white);background:radial-gradient(circle,#f3d7c4,#d8c3c0 60%,#e9e9ef)}
.treat h2{left:282px;top:36px;font-family:"Raleway",sans-serif;font-weight:400;font-size:28px;color:var(--white);white-space:nowrap}
.treat p{left:282px;top:84px;width:300px;font-size:15.5px;line-height:25px;color:var(--white)}
.treat .btn{position:absolute;left:278px;top:172px;width:190px;height:51px;background:var(--white);color:var(--purple);font-size:23px}

/* welcome */
.welcome-title{left:0;top:1076px;width:1200px;text-align:center;font-family:"Raleway",sans-serif;font-weight:300;font-size:42px;color:#555;text-transform:uppercase}
.welcome-title span{color:var(--purple);font-weight:400}
.welcome-copy{left:80px;top:1146px;width:580px;font-size:14.6px;line-height:25px;color:#555}
.welcome-copy p{margin-bottom:25px}
.video{left:690px;top:1148px;width:432px;height:312px;background:linear-gradient(135deg,#5a2e55,#3a1d3c 60%,#6b4a63)}
.play{left:186px;top:126px;width:60px;height:60px;border-radius:50%;background:rgba(255,255,255,.85);display:flex;align-items:center;justify-content:center}

/* appointments */
.appt{left:0;top:1545px;width:1200px;height:301px;background:linear-gradient(90deg,#4b3596 0%,#6b55a8 55%,#7a5e9e 100%)}
.appt .mark{left:88px;top:22px;width:140px;height:250px;border-radius:70px;background:rgba(255,255,255,.9)}
.appt h2{left:0;top:46px;width:1200px;text-align:center;font-family:"Raleway",sans-serif;font-weight:400;font-size:40px;color:var(--white)}
.appt .call{left:0;top:114px;width:1200px;display:flex;justify-content:center;align-items:center;gap:14px;font-family:"Raleway",sans-serif;font-size:30px;color:var(--white)}
.appt .call strong{font-family:"Open Sans",sans-serif;font-weight:700;font-size:30px}
.ring{width:50px;height:50px;border-radius:50%;border:2px solid var(--white);display:flex;align-items:center;justify-content:center}
.appt .or{left:0;top:184px;width:1200px;text-align:center;font-size:20px;color:var(--white)}
.appt .email{left:0;top:220px;width:1200px;display:flex;justify-content:center;align-items:center;gap:8px;font-size:21px;color:var(--white)}

/* news */
.news{left:0;top:1846px;width:1200px;height:495px;background:var(--grey-bg)}
.news h2{left:0;top:52px;width:1200px;text-align:center;font-family:"Raleway",sans-serif;font-weight:300;font-size:42px;color:#555}
.news h2 span{color:var(--purple);font-weight:400}
.card{top:117px;width:234px}
.card .thumb{width:234px;height:146px;border:1px solid #ddd}
.card h3{margin-top:12px;font-weight:400;font-size:17px;line-height:25px;color:var(--purple)}
.card .date{margin-top:6px;display:flex;align-items:center;gap:8px;font-size:14px;color:#777}
.card p{margin-top:8px;font-size:14px;line-height:25px;color:#666}

/* partners */
.badge{top:2395px;height:100px;background:#e4e2ec;border-radius:10px}

/* footer */
.footer{left:0;top:2555px;width:1200px;height:227px;background:var(--purple);color:var(--white)}
.footer .links{left:80px;top:36px;display:flex;gap:28px;font-size:18px}
.footer .soc{top:22px;width:48px;height:48px;border-radius:50%;background:var(--white)}
.footer .rule{left:80px;top:88px;width:1042px;height:1px;background:rgba(255,255,255,.2)}
.footer h4{left:80px;top:107px;font-weight:400;font-size:17px}
.footer .item{top:140px;display:flex;align-items:center;gap:14px;font-size:15px;line-height:25px}
.footer .dot{width:48px;height:48px;border-radius:50%;background:var(--white);display:flex;align-items:center;justify-content:center;flex:none}
.footer .rights{left:890px;top:145px;width:250px;font-size:15px;line-height:25px}
</style>
</head>
<body>

<div class="topbar abs">
  <div class="addr abs">
    <svg width="18" height="24" viewBox="0 0 18 24"><path d="M9 0C4 0 0 4 0 9c0 6.5 9 15 9 15s9-8.5 9-15c0-5-4-9-9-9zm0 12.5A3.5 3.5 0 1 1 9 5.5a3.5 3.5 0 0 1 0 7z" fill="#fff"/></svg>
    Suite 210 / 95 Harlow Street Melbourne 3000
  </div>
  <div class="social abs">Follow us</div>
</div>

<header class="header abs">
  <nav class="nav">
    <a class="active" style="left:412px">HOME</a>
    <a style="left:506px">ABOUT</a>
    <a style="left:616px">SERVICES</a>
    <a style="left:748px">CONTACT</a>
  </nav>
  <div class="head-phone abs">
    <span class="icon-circle"><svg width="24" height="24" viewBox="0 0 24 24"><path d="M6.6 10.8a15.1 15.1 0 0 0 6.6 6.6l2.2-2.2c.3-.3.7-.4 1-.2 1.1.4 2.3.6 3.6.6.6 0 1 .4 1 1V20c0 .6-.4 1-1 1C10.6 21 3 13.4 3 4c0-.6.4-1 1-1h3.5c.6 0 1 .4 1 1 0 1.3.2 2.5.6 3.6.1.3 0 .7-.2 1z" fill="#fff"/></svg></span>
    1300 555 274
  </div>
</header>
<div class="logo-disc abs"></div>
<div class="logo-name abs">Bramble Ridge Podiatry</div>

<section class="hero abs">
  <div class="hero-feet abs" role="img" aria-label="Photo of bare feet raised against a blue beach and sky"></div>
  <h1 class="hero-title abs">Qualified Health Professionals</h1>
  <p class="hero-sub abs">Various foot conditions, including Sports Injuries, Orthotic Therapy &amp; Nail Surgery</p>
  <a class="btn">Contact Us</a>
</section>

<section class="treat general abs">
  <div class="photo abs" role="img" aria-label="Photo of a podiatrist examining a foot"></div>
  <h2 class="abs">General Treatment</h2>
  <p class="abs">Nails, Corns, Callus, Warts, Skin Disorders, Heel pain / Heel Spurs / Arch pain - plantar Fasciitis</p>
  <a class="btn">Read More</a>
</section>
<section class="treat special abs">
  <div class="photo abs" role="img" aria-label="Photo of a nail treatment tool on a toe"></div>
  <h2 class="abs">Specialised Treatments</h2>
  <p class="abs">Diabetic Management, Nail Surgery, Biomechanical Assessment, Gait Analysis, Orthotic Therapy</p>
  <a class="btn">Read More</a>
</section>

<section class="welcome">
  <h2 class="welcome-title abs">Welcome to <span>Bramble Ridge Podiatry</span></h2>
  <div class="welcome-copy abs">
    <p>Bramble Ridge Podiatry is a Podiatry clinic in the heart of Melbourne CBD. We are located between Alder &amp; Quarry Streets in the Meridian Business Centre / Linden Hotel Complex.</p>
    <p>Our podiatrists are fully qualified health professionals who are able to diagnose, treat, manage or help to prevent all medical conditions that affect the feet and lower limb.</p>
    <p>We provide General Podiatry Treatment and some Specialised Services in relation to various foot conditions, including Sports Injuries, Orthotic Therapy and Nail Surgery.</p>
  </div>
  <div class="video abs" role="img" aria-label="Video still of gloved hands treating a foot with podiatry tools">
    <div class="play abs"><svg width="22" height="24" viewBox="0 0 22 24"><path d="M4 2l16 10-16 10z" fill="#4c3494"/></svg></div>
  </div>
</section>

<section class="appt abs">
  <div class="mark abs" role="img" aria-label="Large foot emblem"></div>
  <h2 class="abs">For Appointments or Enquiries</h2>
  <div class="call abs">Please call us on
    <span class="ring"><svg width="22" height="22" viewBox="0 0 24 24"><path d="M6.6 10.8a15.1 15.1 0 0 0 6.6 6.6l2.2-2.2c.3-.3.7-.4 1-.2 1.1.4 2.3.6 3.6.6.6 0 1 .4 1 1V20c0 .6-.4 1-1 1C10.6 21 3 13.4 3 4c0-.6.4-1 1-1h3.5c.6 0 1 .4 1 1 0 1.3.2 2.5.6 3.6.1.3 0 .7-.2 1z" fill="#fff"/></svg></span>
    <strong>1300 555 274</strong></div>
  <div class="or abs">OR</div>
  <div class="email abs">Email:
    <svg width="20" height="16" viewBox="0 0 20 16"><rect x="1" y="1" width="18" height="14" rx="2" fill="none" stroke="#fff" stroke-width="2"/><path d="M1 2l9 7 9-7" fill="none" stroke="#fff" stroke-width="2"/></svg>
    info@brambleridgepodiatry.net</div>
</section>

<section class="news abs">
  <h2 class="abs">LATEST <span>NEWS</span></h2>
  <article class="card abs" style="left:78px">
    <div class="thumb" role="img" aria-label="Photo of a physiotherapist stretching a patient's leg" style="background:linear-gradient(135deg,#e8e4dc,#c9b8a0)"></div>
    <h3>Lorem Ipsum is dummy text and simply printing.</h3>
    <div class="date"><svg width="12" height="12" viewBox="0 0 12 12"><rect x="1" y="2" width="10" height="9" fill="none" stroke="#999"/><path d="M1 5h10" stroke="#999"/></svg>01 August 2016</div>
    <p>Lorem Ipsum is simply dummy text of the printing and type setting industry.</p>
  </article>
  <article class="card abs" style="left:349px">
    <div class="thumb" role="img" aria-label="Photo of feet walking on wet sand" style="background:linear-gradient(180deg,#6a7f8c,#3d4a52)"></div>
    <h3>Lorem Ipsum is dummy text and simply printing.</h3>
    <div class="date"><svg width="12" height="12" viewBox="0 0 12 12"><rect x="1" y="2" width="10" height="9" fill="none" stroke="#999"/><path d="M1 5h10" stroke="#999"/></svg>01 August 2016</div>
    <p>Lorem Ipsum is simply dummy text of the printing and type setting industry.</p>
  </article>
  <article class="card abs" style="left:620px">
    <div class="thumb" role="img" aria-label="Illustration of a foot showing heel pain" style="background:radial-gradient(circle at 55% 65%,#f08a80,#e9b08c 35%,#fff 75%)"></div>
    <h3>Lorem Ipsum is dummy text and simply printing.</h3>
    <div class="date"><svg width="12" height="12" viewBox="0 0 12 12"><rect x="1" y="2" width="10" height="9" fill="none" stroke="#999"/><path d="M1 5h10" stroke="#999"/></svg>01 August 2016</div>
    <p>Lorem Ipsum is simply dummy text of the printing and type setting industry.</p>
  </article>
  <article class="card abs" style="left:890px">
    <div class="thumb" role="img" aria-label="Photo of a clinician consulting with a patient" style="background:linear-gradient(135deg,#f6f0f2,#e69bb4)"></div>
    <h3>Lorem Ipsum is dummy text and simply printing.</h3>
    <div class="date"><svg width="12" height="12" viewBox="0 0 12 12"><rect x="1" y="2" width="10" height="9" fill="none" stroke="#999"/><path d="M1 5h10" stroke="#999"/></svg>01 August 2016</div>
    <p>Lorem Ipsum is simply dummy text of the printing and type setting industry.</p>
  </article>
</section>

<section class="partners">
  <div class="badge abs" style="left:82px;width:222px" role="img" aria-label="Partner badge"></div>
  <div class="badge abs" style="left:346px;width:236px" role="img" aria-label="Partner badge"></div>
  <div class="badge abs" style="left:626px;width:218px" role="img" aria-label="Partner badge"></div>
  <div class="badge abs" style="left:900px;width:214px" role="img" aria-label="Partner badge"></div>
</section>

<footer class="footer abs">
  <nav class="links abs"><span>Home</span><span>About</span><span>Services</span><span>Contact</span></nav>
  <span class="soc abs" style="left:950px"></span>
  <span class="soc abs" style="left:1012px"></span>
  <span class="soc abs" style="left:1074px"></span>
  <div class="rule abs"></div>
  <h4 class="abs">Contact Us</h4>
  <div class="item abs" style="left:76px">
    <span class="dot"><svg width="16" height="22" viewBox="0 0 18 24"><path d="M9 0C4 0 0 4 0 9c0 6.5 9 15 9 15s9-8.5 9-15c0-5-4-9-9-9zm0 12.5A3.5 3.5 0 1 1 9 5.5a3.5 3.5 0 0 1 0 7z" fill="#4c3494"/></svg></span>
    <span>Suite 210 / 95 Harlow<br>Street Melbourne 3000</span>
  </div>
  <div class="item abs" style="left:348px">
    <span class="dot"><svg width="22" height="22" viewBox="0 0 24 24"><path d="M6.6 10.8a15.1 15.1 0 0 0 6.6 6.6l2.2-2.2c.3-.3.7-.4 1-.2 1.1.4 2.3.6 3.6.6.6 0 1 .4 1 1V20c0 .6-.4 1-1 1C10.6 21 3 13.4 3 4c0-.6.4-1 1-1h3.5c.6 0 1 .4 1 1 0 1.3.2 2.5.6 3.6.1.3 0 .7-.2 1z" fill="#4c3494"/></svg></span>
    <strong>1300 555 274</strong>
  </div>
  <div class="item abs" style="left:572px">
    <span class="dot"><svg width="20" height="16" viewBox="0 0 20 16"><rect x="1" y="1" width="18" height="14" rx="2" fill="none" stroke="#4c3494" stroke-width="2"/><path d="M1 2l9 7 9-7" fill="none" stroke="#4c3494" stroke-width="2"/></svg></span>
    <span>info@brambleridgepodiatry.net</span>
  </div>
  <div class="rights abs">© Bramble Ridge Podiatry- 2016.<br>All Rights Reserved.</div>
</footer>

</body>
</html>
```